Flyer-Design für bildenden Künstler
Zielgruppe
Ich bin bildender Künstler, benötige einen außergewöhnlichen, sehr ästhetischen, einzigartigen, als Eyecatcher fungierenden, meine Kunst und Identität repräsentierenden Flyer zum Auslegen, um neue KundInnen zu gewinnen.
Aufgabenstellung
Er soll wenig Text beinhalten (ein Zitat, Anschrift und Kontaktmöglichkeiten, ein kleines statement zu meiner Kunstphilosophie), und Bilder meiner Kunst zeigen. Raum ist mir wichtig, genug Leerräume, damit ein in Szene gesetztes Zitat oder Foto meiner Kunstwerke gut wirken kann. Es soll Lust darauf machen, Anreiz bieten und Interesse wecken, auf meine homepage zu gehen. Die Einzigartigkeit meiner Kunst soll deutlich werden.
Die hochgelandenen Fotos zeigen meine Kunstwerke. Sie können als Hintergrundbild fungieren und dementsprechend auch die ganze Seite ausfüllen, sie können zugeschnitten werden und/oder mit Text überlagert sein. Manche Fotos (zum Beispiel die Kunstwerke mit Rahmen) eignen sich dagegen, sie auf einer ganzen Seite zu zeigen, ohne einen Text dazu. So eine Seite würde ich jedenfalls gerne dabei haben, wo ein Kunstwerk für sich alleine auf einer ganzen Seite dargestellt wird. 1O4A2598 oder 1O4A6076a bieten sich dafür an (diese und alle anderen Fotos sind zum Teil komprimiert und zugeschnitten; falls gewünscht bzw. die Qualität nicht gut ist, kann ich das Originalfoto senden, das unkomprimiert und nicht zugeschnitten ist. Auch kann die Helligkeit oder die Farbqualität verbessert werden, falls notwendig). Nicht alle Kunstbilder müssen verwendet werden.
Ich bin offen für jedes Flyerformat, tendiere zu einem ein 2 oder 3-seitigen Falzflyer hochkant oder im Querformat. Bin aber offen für Ideen und Vorschläge.
Die Texte unter der Datei 'Texte, Adresse, Zitate' enthalten einen kleinen Text, der verwendet werden soll. Unter 'Text für die Titelseite' ist ein Vorschlag für die Titelseite zu finden. Die Adresse muss vollständig erscheinen, und unter 'Zitate' sind mehrere meiner Zitate - auch davon soll eines verwendet werden.
BITTE AUSSCHLIEßLICH DIE FOTOS UND TEXTE VERWENDEN, DIE ICH HOCHGELADEN HABE, UND NICHTS VON MEINEN HOMEPAGES NEHMEN. DANKE!

```html
<!DOCTYPE html>
<html lang="de">
<head>
<meta charset="utf-8">
<title>Faltflyer – Jonas Wendrich Art</title>
<link rel="stylesheet" href="https://fonts.googleapis.com/css2?family=Roboto:wght@700&family=Roboto+Condensed:wght@400;700&family=Source+Serif+4:wght@600&display=swap">
<style>
  :root {
    --backdrop: #dedede;
    --paper: #eeeeee;
    --paper-light: #f5f5f5;
    --teal: #2b4a58;
    --rose: #c6a1b5;
    --coral-light: #b89aaa;
    --blue-art: #3b6f8a;
    --white: #ffffff;
  }
  * { box-sizing: border-box; margin: 0; padding: 0; }
  html, body { width: 755px; height: 1200px; overflow: hidden; }
  body { background: var(--backdrop); position: relative; font-family: "Roboto Condensed", sans-serif; color: var(--teal); }

  .spread { position: absolute; left: 40px; width: 675px; height: 500px; display: flex; box-shadow: 0 6px 18px rgba(0,0,0,.12); }
  .spread--inside { top: 50px; }
  .spread--outside { top: 640px; }
  .panel { position: relative; width: 225px; height: 500px; background: var(--paper); overflow: hidden; }
  .panel:nth-child(2) { background: var(--paper-light); }

  .block { position: absolute; }
  .block--rose { background: var(--rose); }
  .block--teal { background: var(--teal); }
  .rule { position: absolute; height: 6px; background: var(--teal); }
  .rule--rose { background: var(--rose); }

  .artwork { position: absolute; }
  .artwork--framed { background: linear-gradient(135deg, #2f5f78, var(--blue-art) 50%, #274b60); border: 5px solid #3a3a3a; box-shadow: 0 6px 10px rgba(0,0,0,.3); }
  .artwork--coral { background: radial-gradient(ellipse at 70% 55%, #a98597, var(--coral-light) 45%, rgba(238,238,238,0) 75%); }
  .artwork--pile { background: linear-gradient(160deg, #9c7d8c, #b79aa8 50%, #7f6170); }
  .artwork--panel { background: linear-gradient(150deg, #8a5e6a, #6e4552); box-shadow: 0 6px 12px rgba(0,0,0,.3); }

  .statement { position: absolute; font-family: "Source Serif 4", serif; font-weight: 600; font-size: 25px; line-height: 1.13; color: var(--teal); }
  .mark { background: var(--rose); padding: 0 3px; }

  .quote { position: absolute; z-index: 1; font-family: "Roboto Condensed", sans-serif; font-weight: 700; font-size: 9.5px; line-height: 1.45; text-transform: uppercase; text-align: center; color: var(--teal); }
  .quote-mark { position: absolute; z-index: 0; font-family: "Source Serif 4", serif; font-weight: 600; font-size: 110px; line-height: 1; color: var(--rose); }

  .cover-name { position: absolute; left: 14px; top: 28px; z-index: 1; font-family: "Roboto", sans-serif; font-weight: 700; font-size: 40px; line-height: 1.1; letter-spacing: 1px; color: var(--teal); }

  .contact { position: absolute; left: 38px; top: 330px; font-family: "Roboto Condensed", sans-serif; font-size: 10px; line-height: 1.4; color: var(--teal); }
  .contact strong { font-weight: 700; }
  .contact p + p { margin-top: 10px; }

  .band-quote { position: absolute; left: 84px; top: 368px; width: 122px; font-family: "Roboto Condensed", sans-serif; font-weight: 700; font-size: 9px; line-height: 1.45; text-transform: uppercase; text-align: center; color: var(--white); }
</style>
</head>
<body>

<section class="spread spread--inside">
  <div class="panel panel--statement">
    <div class="block block--rose" style="left:28px;top:30px;width:200px;height:160px;"></div>
    <div class="artwork artwork--framed" role="img" aria-label="Gerahmtes Kunstwerk aus blau eingefärbten, porösen Materialstücken" style="left:55px;top:75px;width:175px;height:125px;border-right:none;"></div>
    <p class="statement" style="left:26px;top:240px;width:192px;">In meiner Kunst gebe ich Material und Vergangenem eine neue <span class="mark">Sinnhaftigkeit.</span></p>
  </div>

  <div class="panel panel--quotes">
    <div class="block block--rose" style="left:0;top:30px;width:60px;height:70px;"></div>
    <div class="artwork artwork--framed" role="img" aria-label="Fortsetzung des gerahmten blauen Kunstwerks" style="left:0;top:75px;width:95px;height:125px;border-left:none;"></div>
    <span class="quote-mark" style="left:100px;top:10px;">”</span>
    <p class="quote" style="left:30px;top:40px;width:170px;">Kunst ermöglicht einen Blick über den Tellerrand von Ursache und Wirkung hinaus.</p>
    <span class="quote-mark" style="left:95px;top:255px;">”</span>
    <p class="quote" style="left:35px;top:288px;width:160px;">Kunst unterstreicht deinen guten Geschmack. Es zeugt davon, dass du Weitblick besitzt, und offen für neue Erfahrungen bist.</p>
    <div class="rule" style="left:65px;top:378px;width:95px;"></div>
  </div>

  <div class="panel panel--cover">
    <div class="artwork artwork--coral" role="img" aria-label="Nahaufnahme einer rosafarbenen, korallenartigen Skulptur" style="left:85px;top:0;width:140px;height:500px;"></div>
    <p class="cover-name">JONAS<br>WENDRICH<br>ART</p>
    <div class="rule" style="left:14px;top:300px;width:110px;"></div>
  </div>
</section>

<section class="spread spread--outside">
  <div class="panel panel--contact">
    <div class="block block--teal" style="left:28px;top:30px;width:102px;height:180px;"></div>
    <div class="artwork artwork--pile" role="img" aria-label="Nahaufnahme gehäufter, rosafarbener poröser Materialstücke" style="left:38px;top:70px;width:130px;height:185px;"></div>
    <div class="block block--rose" style="left:100px;top:250px;width:72px;height:45px;"></div>
    <div class="contact">
      <p><strong>JONAS WENDRICH</strong><br>Ahornweg 14<br>79104 Lindenau</p>
      <p>wendrich-art@mailpost.de<br>(+49) 0761 5550 1234<br>www.wendrich-art.de</p>
    </div>
    <div class="rule" style="left:38px;top:440px;width:80px;"></div>
  </div>

  <div class="panel panel--philosophy">
    <p class="statement" style="left:16px;top:22px;width:205px;">Seit jeher<br>fasziniert<br>mich die<br><span class="mark">Transformation</span><br>eines Zustandes<br>in einen<br>anderen.</p>
    <div class="rule" style="left:16px;top:245px;width:62px;"></div>
    <p class="statement" style="left:16px;top:262px;width:205px;">Das ganze<br>Leben ist eine<br>fortwährende<br><span class="mark">Veränderung,</span><br>nichts bleibt,<br>wie es ist.</p>
  </div>

  <div class="panel panel--artwork">
    <div class="block block--teal" style="left:78px;top:30px;width:132px;height:400px;"></div>
    <div class="artwork artwork--panel" role="img" aria-label="Rechteckiges Wandobjekt aus dunkelrosa porösem Material" style="left:18px;top:100px;width:130px;height:215px;"></div>
    <p class="band-quote">Die Suche nach der Wahrheit führt nur über die Distanz zur Realität.</p>
    <div class="rule rule--rose" style="left:100px;top:412px;width:80px;"></div>
  </div>
</section>

</body>
</html>
```